Signage Design Project

Busisness is a bakery and deli long time owned by the Tavel family. Want to develop a new outside sign that communicates it is a deli and a bakery but keeps the tavel name in the design.

The sign when produced will be about 10' by 3' . It is not lighted at present but could be if it were advantageous.

The name of the store is:

Tavel's Harbor Lane Bakery and Deli. The concept is to have a new,modern sign that reinforces that it is a deli and a bakery, as most people only know about the bakery side of the business
Updates

The name Tavel is just a reinforcer so the people kno it is still in the family.  The emphasis should be on the HARBOR LANE BAKERY and DELI

Target Market(s)

Small business breakfast and lunch customers

Industry/Entity Type

Bakery

Requirements
Must have
• Great impact from the road. Communicate that it is a deli and a bakery. Keep the Tavel name but need not be a major design element

```html
<!DOCTYPE html>
<html lang="en">
<head>
<meta charset="utf-8">
<title>Tavel's Harbor Lane Bakery and Deli – Storefront Sign</title>
<link rel="stylesheet" href="https://fonts.googleapis.com/css2?family=Righteous&display=swap">
<style>
  :root {
    --sign-maroon: #6d262a;
    --sign-yellow: #f7ec4a;
    --flourish-gold: #e9c85a;
  }
  * { margin: 0; padding: 0; box-sizing: border-box; }
  html, body {
    width: 1200px;
    height: 360px;
    overflow: hidden;
    background: var(--sign-maroon);
  }
  .sign {
    position: relative;
    width: 1200px;
    height: 360px;
    background: var(--sign-maroon);
    font-family: "Righteous", sans-serif;
    font-weight: 400;
    font-style: normal;
    color: var(--sign-yellow);
  }
  .flourish {
    position: absolute;
    top: 16px;
    width: 62px;
    height: 328px;
  }
  .flourish--left { left: 6px; }
  .flourish--right { right: 6px; }

  .name-line {
    position: absolute;
    top: 52px;
    left: 0;
    width: 1200px;
    display: flex;
    justify-content: center;
    align-items: baseline;
    gap: 22px;
    font-weight: 400;
    line-height: 1;
    white-space: nowrap;
  }
  .family-name { font-size: 50px; }
  .place-name { font-size: 84px; }

  .trade-line {
    position: absolute;
    top: 176px;
    left: 0;
    width: 1200px;
    text-align: center;
    font-size: 134px;
    line-height: 1;
    letter-spacing: 3px;
    white-space: nowrap;
  }
</style>
</head>
<body>
  <div class="sign">
    <svg class="flourish flourish--left" viewBox="0 0 62 328" role="img" aria-label="Decorative gold scroll flourish border">
      <rect x="0" y="0" width="62" height="328" rx="10" fill="var(--flourish-gold)" opacity="0.18"/>
    </svg>

    <h1 class="name-line">
      <span class="family-name">Tavel's</span>
      <span class="place-name">Harbor Lane</span>
    </h1>

    <p class="trade-line">Bakery and Deli</p>

    <svg class="flourish flourish--right" viewBox="0 0 62 328" role="img" aria-label="Decorative gold scroll flourish border">
      <rect x="0" y="0" width="62" height="328" rx="10" fill="var(--flourish-gold)" opacity="0.18"/>
    </svg>
  </div>
</body>
</html>
```